Website Refresh

I'm looking to refresh my Squarespace website. www.derekmulvane.com

I am pretty happy with the content but would like a better navigation bar, livelier color choices, consistent type faces, and a more modern look. I am willing to pay extra to implement suggested improvements that would make the site more appealing

```html
<!DOCTYPE html>
<html lang="en">
<head>
<meta charset="utf-8">
<title>Keystone – Derek Mulvane</title>
<link href="https://fonts.googleapis.com/css2?family=Lato:ital,wght@0,400;0,700;0,900;1,400&display=swap" rel="stylesheet">
<style>
:root{
  --navy:#0e3552;
  --royal:#1a10a0;
  --orange:#fb6a07;
  --grey:#e4e5e7;
  --text:#4a4a4a;
  --footer:#1c1c1c;
  --white:#fff;
}
*{margin:0;padding:0;box-sizing:border-box}
html,body{width:1200px;height:4566px;overflow:hidden}
body{position:relative;font-family:"Lato",sans-serif;color:var(--text);background:var(--white)}
.abs{position:absolute}
.btn{position:absolute;display:flex;align-items:center;justify-content:center;background:var(--orange);color:var(--white);font-weight:700;font-size:16px;text-transform:uppercase;letter-spacing:.3px}
.heading{font-weight:900;text-transform:uppercase;letter-spacing:.5px;line-height:1.05}
.photo{position:absolute}
/* header */
.brand{left:74px;top:26px}
.brand-name{font-size:52px;font-weight:900;color:var(--navy);letter-spacing:-1px;line-height:1}
.brand-tag{font-size:13px;color:#555;line-height:1.3;margin-left:6px;width:230px}
.nav{left:0;top:131px;width:1200px;height:60px;background:var(--navy);display:flex;align-items:center;justify-content:center;gap:25px}
.nav a{color:var(--white);font-size:12px;font-weight:700;text-decoration:none;text-transform:uppercase;letter-spacing:.3px}
/* hero */
.hero{left:0;top:191px;width:1200px;height:722px;background:linear-gradient(180deg,#c58d5c 0%,#b98358 40%,#5a4438 75%,#2b2a2e 100%)}
.hero-title{left:0;top:228px;width:1200px;text-align:center;color:var(--white);font-size:56px}
.hero-sub{left:0;top:352px;width:1200px;text-align:center;color:var(--white);font-size:23px;line-height:33px;font-weight:700}
/* about */
.section-title{color:var(--navy);font-size:42px}
.rule{height:3px;background:#bcbcbc;width:136px}
.body-copy{font-size:15px;line-height:28.5px;color:var(--text)}
/* blue */
.band-blue{left:0;width:1200px;background:var(--royal)}
.white{color:var(--white)}
.checks{list-style:none}
.checks li{display:flex;align-items:center;gap:16px;font-size:16px;height:39px;color:var(--white)}
/* videos */
.card{position:absolute;top:2163px;width:328px;height:239px;background:linear-gradient(160deg,#6f8c74,#3c4f5a 60%,#1e2a33)}
.card .play{position:absolute;left:142px;top:80px}
.card .name{position:absolute;left:0;bottom:0;width:100%;height:45px;background:var(--royal);color:var(--white);font-size:21px;font-weight:700;display:flex;align-items:center;justify-content:center}
/* footer */
.footer{left:0;top:4201px;width:1200px;height:365px;background:var(--footer)}
.foot-h{color:var(--white);font-weight:700;font-size:18px}
.foot-links a{display:block;color:#e6e6e6;font-size:15px;text-decoration:none;height:31.3px;line-height:31px}
</style>
</head>
<body>

<!-- header -->
<div class="abs brand">
  <div class="brand-name">KEYSTONE</div>
  <div class="brand-tag">Private advisory boards for CEOs, executives and business owners.</div>
</div>
<a class="btn" style="left:954px;top:46px;width:172px;height:50px;text-decoration:none">Contact Derek</a>

<nav class="abs nav">
  <a href="#">About the Group</a>
  <a href="#">Member Video Testimonials</a>
  <a href="#">Testimonials</a>
  <a href="#">Success Stories</a>
  <a href="#">Derek's Blog</a>
  <a href="#">Derek Mulvane Bio</a>
  <a href="#">Join the Group</a>
</nav>

<!-- hero -->
<div class="abs hero" role="img" aria-label="Group photo of the CEO members gathered in a hotel meeting room"></div>
<h1 class="abs heading hero-title">Turning good CEOs into<br>great CEOs</h1>
<p class="abs hero-sub">Our award winning CEOs will help you make better decisions for your<br>company, family, and community .</p>
<svg class="abs" style="left:0;top:850px" width="1200" height="75" viewBox="0 0 1200 75">
  <polygon points="0,63 1200,20 1200,75 0,75" fill="#fff"/>
  <polygon points="620,42 1200,8 1200,70 1180,66" fill="var(--navy)"/>
  <polygon points="620,42 1180,66 1200,70 1200,72 900,60" fill="#5d7e96"/>
</svg>

<!-- about -->
<div class="photo" style="left:74px;top:987px;width:513px;height:440px;background:linear-gradient(135deg,#8a8d86,#4f4f4a 55%,#2c2b29)" role="img" aria-label="Members seated around a boardroom table during a meeting"></div>
<h2 class="abs heading section-title" style="left:615px;top:980px">About Keystone</h2>
<div class="abs rule" style="left:615px;top:1046px"></div>
<div class="abs body-copy" style="left:615px;top:1071px;width:510px">
  <p>After many years in the business world as the founder/CEO of six for-profit and five not-for-profit corporations, I understand the huge responsibility you have for making the right decisions for your company, the personal well-being of your employees and yourself.</p>
  <p style="margin-top:10px">Our Keystone group is made up of 15 other smart CEOs who have been where you are. &nbsp;We meet monthly in a safe, confidential environment to discuss critical business decisions, opportunities, and challenges.</p>
</div>
<div class="btn" style="left:615px;top:1375px;width:172px;height:50px">Read More</div>

<!-- membership / leader -->
<div class="abs band-blue" style="top:1503px;height:500px"></div>
<h3 class="abs white" style="left:74px;top:1576px;font-size:27px;font-weight:700;line-height:35px">Membership is by invitation<br>only for those who:</h3>
<ul class="abs checks" style="left:74px;top:1665px">
  <li><svg width="18" height="18" viewBox="0 0 18 18"><circle cx="9" cy="9" r="9" fill="#fff"/><path d="M5 9.3l2.7 2.6L13 6.5" stroke="var(--royal)" stroke-width="2.2" fill="none"/></svg>Open to being challenged</li>
  <li><svg width="18" height="18" viewBox="0 0 18 18"><circle cx="9" cy="9" r="9" fill="#fff"/><path d="M5 9.3l2.7 2.6L13 6.5" stroke="var(--royal)" stroke-width="2.2" fill="none"/></svg>Commit to double-digit growth</li>
  <li><svg width="18" height="18" viewBox="0 0 18 18"><circle cx="9" cy="9" r="9" fill="#fff"/><path d="M5 9.3l2.7 2.6L13 6.5" stroke="var(--royal)" stroke-width="2.2" fill="none"/></svg>Ongoing learning</li>
  <li><svg width="18" height="18" viewBox="0 0 18 18"><circle cx="9" cy="9" r="9" fill="#fff"/><path d="M5 9.3l2.7 2.6L13 6.5" stroke="var(--royal)" stroke-width="2.2" fill="none"/></svg>Giving &amp; receiving honest feedback</li>
</ul>
<p class="abs white" style="left:74px;top:1839px;width:410px;font-size:15.5px;line-height:28px">f you are lonely with no one you can trust to talk through tough decisions. If you don't have the right people in the right seats.</p>
<div class="photo" style="left:525px;top:1585px;width:267px;height:336px;background:linear-gradient(160deg,#9aa0a5,#c9ccd0 45%,#6e6a68)" role="img" aria-label="Portrait of Derek Mulvane speaking to the group"></div>
<h2 class="abs heading white" style="left:817px;top:1604px;font-size:44px">Seasoned<br>Leader</h2>
<p class="abs white" style="left:817px;top:1709px;width:290px;font-size:15.5px;line-height:27.5px">My purpose is to use my gifts and life lessons to help ignite, inspire and transform the lives of leaders of leaders.</p>
<div class="btn" style="left:817px;top:1840px;width:209px;height:51px">More About Derek</div>

<!-- video testimonials -->
<h2 class="abs heading section-title" style="left:0;top:2054px;width:1200px;text-align:center">Member Video Testimonials</h2>
<div class="abs rule" style="left:532px;top:2117px"></div>
<svg class="abs" style="left:40px;top:2265px" width="22" height="36" viewBox="0 0 22 36"><path d="M18 2L4 18l14 16" stroke="#444" stroke-width="3" fill="none"/></svg>
<svg class="abs" style="left:1138px;top:2265px" width="22" height="36" viewBox="0 0 22 36"><path d="M4 2l14 16L4 34" stroke="#444" stroke-width="3" fill="none"/></svg>
<div class="card" style="left:74px" role="img" aria-label="Video still of a member interview">
  <svg class="play" width="46" height="46" viewBox="0 0 46 46"><circle cx="23" cy="23" r="20" stroke="#fff" stroke-width="3" fill="none"/><polygon points="18,13 33,23 18,33" fill="#fff"/></svg>
  <div class="name">Grant Hollis</div>
</div>
<div class="card" style="left:436px" role="img" aria-label="Video still of a member interview">
  <svg class="play" width="46" height="46" viewBox="0 0 46 46"><circle cx="23" cy="23" r="20" stroke="#fff" stroke-width="3" fill="none"/><polygon points="18,13 33,23 18,33" fill="#fff"/></svg>
  <div class="name">Martin Ashby</div>
</div>
<div class="card" style="left:798px" role="img" aria-label="Video still of a member interview">
  <svg class="play" width="46" height="46" viewBox="0 0 46 46"><circle cx="23" cy="23" r="20" stroke="#fff" stroke-width="3" fill="none"/><polygon points="18,13 33,23 18,33" fill="#fff"/></svg>
  <div class="name">Nolan Trask</div>
</div>
<div class="btn" style="left:401px;top:2455px;width:399px;height:50px">See More Member Video Testimonials</div>

<!-- methodology -->
<svg class="abs" style="left:0;top:2561px" width="1200" height="660" viewBox="0 0 1200 660">
  <rect x="0" y="0" width="1200" height="660" fill="var(--grey)"/>
  <polygon points="0,0 1200,0 1200,18 0,84" fill="#fff"/>
  <polygon points="0,0 700,38 0,84" fill="var(--navy)"/>
  <polygon points="0,580 1200,560 1200,660 0,660" fill="#fff"/>
  <polygon points="520,586 1200,568 1200,660 1180,655" fill="var(--navy)"/>
  <polygon points="520,586 1180,655 1200,660 1200,662 900,640" fill="#5d7e96"/>
</svg>
<svg class="abs" style="left:74px;top:2738px" width="472" height="298" viewBox="42 1545 266 168" font-family="Lato, sans-serif">
  <polygon points="84,1545 146,1545 146,1617 188,1663 115,1713 42,1663 84,1617" fill="var(--royal)"/>
  <polygon points="234,1545 307,1597 265,1640 265,1713 203,1713 203,1640 161,1597" fill="var(--navy)"/>
  <text x="118" y="1649" text-anchor="middle" font-size="21" font-weight="700" fill="#fff">-4.7%</text>
  <text x="118" y="1666" text-anchor="middle" font-size="8.5" fill="#fff">Non- Member</text>
  <text x="118" y="1678" text-anchor="middle" font-size="8.5" fill="#fff">Companies</text>
  <text x="234" y="1605" text-anchor="middle" font-size="21" font-weight="700" fill="#fff">+4.6%</text>
  <text x="234" y="1623" text-anchor="middle" font-size="8.5" fill="#fff">Keystone Member</text>
  <text x="234" y="1636" text-anchor="middle" font-size="8.5" fill="#fff">Companies</text>
</svg>
<h2 class="abs heading section-title" style="left:615px;top:2692px">Proven Keystone<br>Methodology</h2>
<p class="abs" style="left:615px;top:2799px;width:520px;font-size:19px;line-height:29.5px;color:var(--royal)">According to Harlow &amp; Pierce, in 2020 Keystone member companies outperformed the competition and grew 4.6% compared to nonmember companies who shrunk -4.7% .</p>
<p class="abs body-copy" style="left:615px;top:2929px;width:515px">Not every CEO Peer Group, nor every Keystone group, is the same. Learn why ours is different and find out if you might be a fit for our limited space.</p>
<div class="btn" style="left:615px;top:3031px;width:241px;height:50px">Membership Criteria</div>

<!-- testimonials -->
<h2 class="abs heading section-title" style="left:0;top:3270px;width:1200px;text-align:center">Testimonials</h2>
<svg class="abs" style="left:54px;top:3440px" width="22" height="36" viewBox="0 0 22 36"><path d="M18 2L4 18l14 16" stroke="#444" stroke-width="3" fill="none"/></svg>
<svg class="abs" style="left:1126px;top:3440px" width="22" height="36" viewBox="0 0 22 36"><path d="M4 2l14 16L4 34" stroke="#444" stroke-width="3" fill="none"/></svg>
<p class="abs" style="left:100px;top:3364px;width:1000px;text-align:center;font-style:italic;font-size:15px;line-height:31.5px;color:var(--text)">"The guidance I got. The people I met. The wisdom they brought. Without it, I wouldn't have been able to successfully sell my company for $50 million dollars. Based on my $75,000 membership, I received a 40,000 to 1 ROI. At the center of it is Derek who not only brought together a brilliant group of people but makes sure we all get what we need from each other. Drawing on a ton of personal experience, he's a huge asset to any entrepreneur.""</p>
<p class="abs" style="left:0;top:3515px;width:1200px;text-align:center;font-size:16px;color:var(--royal)">- Evan Marsh, CEO, Brightline Audio</p>
<div class="btn" style="left:480px;top:3584px;width:240px;height:50px">View All Testimonials</div>

<!-- peer ceos -->
<div class="abs band-blue" style="top:3705px;height:496px"></div>
<div class="photo" style="left:74px;top:3788px;width:422px;height:337px;background:linear-gradient(180deg,#4c7a8a,#35414a 45%,#1a1d22)" role="img" aria-label="Group photo of the peer CEOs in front of a mural"></div>
<h2 class="abs heading white" style="left:534px;top:3833px;font-size:42px">Impressive Peer CEOs</h2>
<p class="abs white" style="left:534px;top:3896px;width:600px;font-size:15px;line-height:32px">Join a diverse blend of 17 seasoned men and women CEOs from some of San Diego's finest companies. The group features award-winning private and venture-backed companies.</p>
<div class="btn" style="left:534px;top:4024px;width:209px;height:51px">Our Members</div>

<!-- footer -->
<footer class="abs footer"></footer>
<div class="abs" style="left:74px;top:4296px">
  <div style="font-size:48px;font-weight:900;color:#8a8a8a;letter-spacing:-1px;line-height:1">KEYSTONE</div>
  <div style="font-size:12px;color:#8a8a8a;line-height:1.3;width:220px;margin-left:6px">Private advisory boards for CEOs, executives and business owners.</div>
</div>
<p class="abs" style="left:74px;top:4405px;font-size:13px;line-height:26px;color:#e6e6e6">Copyright © 2022. Company Name<br>All Rights Reserved</p>
<div class="abs foot-h" style="left:381px;top:4260px">Site Map</div>
<div class="abs foot-links" style="left:381px;top:4289px">
  <a href="#">About The Group</a>
  <a href="#">Member Video Testimonials</a>
  <a href="#">Testimonials</a>
  <a href="#">Success Stories</a>
  <a href="#">Derek's Blog</a>
  <a href="#">Derek Mulvane Bio</a>
  <a href="#">Join The Group</a>
</div>
<div class="abs foot-h" style="left:705px;top:4260px">Email Sign Up</div>
<div class="abs" style="left:705px;top:4311px;width:254px;height:46px;background:#fff;border:1px solid #ccc;font-size:14px;color:#444;padding:14px 14px">Email Address</div>
<div class="btn" style="left:973px;top:4311px;width:153px;height:46px;font-style:italic;text-transform:none;font-size:17px">Subscribe</div>
<div class="abs foot-h" style="left:705px;top:4387px">Follow Us</div>
<svg class="abs" style="left:705px;top:4430px" width="200" height="26" viewBox="0 0 200 26">
  <circle cx="10" cy="13" r="9" fill="#fff"/>
  <circle cx="53" cy="13" r="9" fill="#fff"/>
  <circle cx="95" cy="13" r="9" fill="#fff"/>
  <circle cx="138" cy="13" r="9" fill="#fff"/>
  <circle cx="180" cy="13" r="9" fill="#fff"/>
</svg>

</body>
</html>
```